Company Website for Varnoth Signal, an open source data analytics company focused on relationship and li

I need a company/brand website for our new startup, Varnoth Signal LLC. We are a company focused on using life pattern analysis techniques, looking at relationships and how relationships, attributes, and activity cluster to infer aggregate information about individuals and groups. Our focus is on improving the digital advertising market.

We have a company logo which I will upload shortly.

Target Market(s)

Digital Advertising

Number of Pages Required

3 page

Font styles to use
Sans Serif

Requirements
Must have
• An main page, about us, contact page.
Nice to have
• Varnoth Signal relies on state of the art analytics applied to a the digital marketing space. While it is heavy in science, we also understand the art of influence. The website should have a scientific edge but also a flair that illustrates our focus on applying the hard science and analytics to influencing the behavior of people.

```html
<!DOCTYPE html>
<html lang="en">
<head>
<meta charset="utf-8">
<title>Varnoth Signal</title>
<link href="https://fonts.googleapis.com/css2?family=Montserrat:wght@400;500;600;700&family=Open+Sans:ital,wght@0,400;0,600;1,400;1,600&display=swap" rel="stylesheet">
<style>
:root{
  --blue:#1f73c4;
  --blue-bright:#2a85e0;
  --ink:#ffffff;
  --muted:#c9c9c9;
  --dark:#232323;
  --darker:#1b1b1b;
  --card:#1d1d1d;
  --line:#3a3a3a;
}
*{margin:0;padding:0;box-sizing:border-box}
html,body{width:1200px;height:3442px;overflow:hidden;background:var(--dark);color:var(--ink);font-family:"Open Sans",Arial,sans-serif}
.page{position:relative;width:1200px;height:3442px}
.abs{position:absolute}
h1,h2,h3,h4,.nav,.btn,.logo{font-family:"Montserrat",Arial,sans-serif}

/* hero */
.hero{left:0;top:0;width:1200px;height:654px;background:linear-gradient(100deg,#3a3632 0%,#5a524a 40%,#4a4540 65%,#2f2d2b 100%)}
.hero-shade{inset:0;background:rgba(20,20,20,.45)}
.logo{left:116px;top:18px;display:flex;align-items:center;gap:8px;font-weight:700;font-size:24px;color:var(--blue-bright)}
.logo-dot{width:14px;height:14px;border-radius:50%;background:var(--blue-bright)}
.nav{right:60px;top:32px;display:flex;align-items:center;gap:24px;font-size:13px;font-weight:500}
.nav a{color:#fff;text-decoration:none}
.nav a.active{color:var(--blue-bright);border-bottom:1px solid var(--blue-bright);padding-bottom:2px}
.nav .cart{width:26px;height:26px;border-radius:50%;background:var(--blue);display:flex;align-items:center;justify-content:center}
.hero-content{left:119px;top:252px;display:flex;flex-direction:column;align-items:flex-start}
.tagline{height:56px;padding:0 18px;border:2px solid #fff;display:flex;align-items:center;font-family:"Montserrat",sans-serif;font-weight:500;font-size:21px;letter-spacing:.5px;margin-bottom:4px}
.hero-title{font-size:41px;line-height:62px;font-weight:700;letter-spacing:.5px;white-space:nowrap;margin-bottom:12px}
.btn{display:flex;align-items:center;justify-content:center;font-weight:600;font-size:14px;letter-spacing:1px;color:#fff}
.btn-primary{width:172px;height:48px;background:var(--blue)}
.arrow{top:322px;width:30px;height:40px}
.dots{left:570px;top:576px;display:flex;gap:6px}
.dots i{width:11px;height:11px;border-radius:50%;background:#cfcfcf}
.dots i.on{background:var(--blue-bright)}
.notch{left:570px;top:620px}

/* about */
.about{left:0;top:654px;width:1200px;height:608px;background:var(--dark)}
.section-title{width:1200px;text-align:center;font-weight:500;font-size:40px;letter-spacing:1px}
.tabs{left:110px;top:128px;display:flex;border-left:1px solid var(--line);font-size:11px;font-family:"Montserrat",sans-serif}
.tabs span{padding:14px 26px;border-right:1px solid var(--line);color:#ddd}
.city{left:110px;top:208px;width:475px;height:161px;background:linear-gradient(180deg,#7fa6c9 0%,#5d7fa0 45%,#2e4762 62%,#6f90b2 100%)}
.about-heading{left:110px;top:392px;font-size:28px;font-weight:500;letter-spacing:.5px}
.about-copy{left:110px;top:436px;width:475px;font-size:11.5px;line-height:19px;color:var(--muted)}
.steps{left:612px;top:216px;width:490px}
.step{position:relative;height:128px;padding-left:83px}
.step-num{position:absolute;left:0;top:0;width:56px;height:56px;border-radius:50%;background:var(--blue);display:flex;align-items:center;justify-content:center;font-family:"Montserrat",sans-serif;font-size:26px;font-weight:500;box-shadow:0 0 0 4px #2e2e2e}
.step h4{font-size:11px;font-weight:500;color:var(--blue-bright);margin:4px 0 6px}
.step p{font-size:11px;line-height:19px;color:var(--muted)}

/* team */
.team{left:0;top:1262px;width:1200px;height:940px;background:#202020}
.team-sub{width:1200px;text-align:center;font-style:italic;font-weight:600;font-size:19px}
.card{width:308px;height:347px;background:var(--card)}
.card .photo{position:absolute;left:0;top:0;width:308px;height:211px}
.card .badge{position:absolute;left:134px;top:184px;width:40px;height:40px;border-radius:50%;background:var(--blue);border:3px solid #fff;display:flex;align-items:center;justify-content:center}
.card h3{position:absolute;left:0;top:238px;width:308px;text-align:center;font-size:15px;font-weight:500;letter-spacing:.5px}
.card .rule{position:absolute;left:129px;top:262px;width:50px;height:2px;background:var(--blue)}
.card p{position:absolute;left:34px;top:276px;width:240px;text-align:center;font-size:11px;line-height:19px;color:#ddd}
.card.featured{background:var(--blue)}
.card.featured .photo{height:154px}
.card.featured .badge{top:128px}
.card.featured h3{top:180px}
.card.featured .rule{top:204px;background:#fff}
.card.featured p{top:218px}
.socials{position:absolute;left:108px;top:296px;display:flex;gap:8px}
.socials i{width:26px;height:26px;border:1px solid #fff;border-radius:50%}

/* banner */
.banner{left:0;top:2202px;width:1200px;height:459px;background:linear-gradient(120deg,#2a6fb8 0%,#3b86d1 45%,#2d76c2 100%)}
.banner h2{width:1200px;text-align:center;font-size:28px;font-weight:600;letter-spacing:2px;line-height:42px}
.btn-outline{left:542px;top:285px;width:116px;height:38px;border:1px solid #fff;font-size:12px;font-weight:500}

/* analytics */
.analytics-head{left:0;top:2661px;width:1200px;height:149px;background:#232323}
.analytics-head h2{width:1200px;text-align:center;font-weight:500;font-size:31px;letter-spacing:1px}
.analytics-head p{width:1200px;text-align:center;font-style:italic;font-size:19px}
.laptop{left:0;top:2810px;width:378px;height:287px;background:linear-gradient(135deg,#8a7d6c 0%,#c8c2b8 40%,#5f5a52 100%)}
.analytics-copy{left:378px;top:2810px;width:822px;height:287px;background:var(--blue);padding:42px 150px 0 26px;font-size:19px;line-height:39.5px;letter-spacing:.3px}
.stat-row{left:0;top:3097px;width:1200px;height:103px;display:flex}
.stat{width:400px;background:#1f1f1f;text-align:center;padding-top:26px}
.stat.active{background:var(--blue)}
.stat small{display:block;font-size:9px;font-family:"Montserrat",sans-serif;letter-spacing:.3px}
.stat strong{display:block;font-family:"Montserrat",sans-serif;font-size:27px;font-weight:500;letter-spacing:1px;margin-top:2px}

/* footer */
.footer{left:0;top:3200px;width:1200px;height:242px;background:var(--darker)}
.foot-col{font-size:10.5px;line-height:16px;color:#ddd}
.foot-col h4{font-family:"Open Sans",sans-serif;font-weight:400;font-size:11px;color:var(--blue-bright);margin-bottom:6px}
.foot-col .brand{color:var(--blue-bright)}
.foot-social{display:flex;gap:9px;margin-top:22px}
.foot-social i{width:26px;height:26px;border:1px solid #777;border-radius:50%}
.subscribe{margin-top:16px;width:140px;height:26px;border:1px solid #666;border-radius:13px;display:flex;align-items:center;justify-content:space-between;padding:0 8px 0 12px;color:#888;font-size:9px}
.bottom-bar{left:0;top:195px;width:1200px;height:47px;background:#151515;border-top:1px solid #2c2c2c}
</style>
</head>
<body>
<div class="page">

  <header class="hero abs">
    <div class="hero-bg abs" role="img" aria-label="Photo of a smiling businessman working at a laptop in an office" style="inset:0"></div>
    <div class="hero-shade abs"></div>
    <div class="logo abs"><span class="logo-dot"></span>Varnoth Signal</div>
    <nav class="nav abs">
      <a class="active">Home</a><a>About us</a><a>Our Team</a><a>Our Products</a><a>Blog</a><a>Contact</a>
      <span class="cart"><svg width="12" height="12" viewBox="0 0 12 12"><path d="M1 2h2l1.5 6h5L11 4H4" fill="none" stroke="#fff" stroke-width="1.3"/><circle cx="5" cy="10.3" r="1" fill="#fff"/><circle cx="9" cy="10.3" r="1" fill="#fff"/></svg></span>
      <svg width="12" height="12" viewBox="0 0 12 12"><circle cx="5" cy="5" r="3.5" fill="none" stroke="#fff" stroke-width="1.5"/><path d="M7.5 7.5L11 11" stroke="#fff" stroke-width="1.5"/></svg>
    </nav>
    <div class="hero-content abs">
      <div class="tagline">THE MOST ADVANCED PULL-UP SUSPENSIONS</div>
      <h1 class="hero-title">IMPROVING THE DIGITAL ADVERTISING<br>MARKET</h1>
      <div class="btn btn-primary">OUR PRODUCTS</div>
    </div>
    <svg class="arrow abs" style="left:34px" viewBox="0 0 30 40"><path d="M20 8L9 20l11 12" fill="none" stroke="#fff" stroke-width="4"/></svg>
    <svg class="arrow abs" style="left:1124px" viewBox="0 0 30 40"><path d="M10 8l11 12-11 12" fill="none" stroke="#fff" stroke-width="4"/></svg>
    <div class="dots abs"><i class="on"></i><i></i><i></i></div>
    <svg class="notch abs" width="60" height="34" viewBox="0 0 60 34"><path d="M0 34L30 6l30 28z" fill="var(--blue)"/><path d="M22 24l8-8 8 8" fill="none" stroke="#fff" stroke-width="2"/></svg>
  </header>

  <section class="about abs">
    <h2 class="section-title abs" style="top:26px">ABOUT US</h2>
    <div class="tabs abs"><span>Our Story</span><span>Mission &amp; Vision</span><span>Company Values</span></div>
    <div class="city abs" role="img" aria-label="City skyline reflected in water under a blue sky"></div>
    <h3 class="about-heading abs">DIGITAL ADVERTISING MARKET</h3>
    <p class="about-copy abs">Lorem ipsum dolor sit amet, consectetur adipiscing elit. Aenean egestas eu leo nec eleifend. Nulla sapien turpis, convallis ac ultrices sed, aliquam sit amet arcu. Phasellus est orci, bibendum consequat quam sit amet, facilisis pharetra nisl. Nullam ultrices mi quam, ut volutpat magna suscipit eget.</p>
    <div class="steps abs">
      <div class="step"><div class="step-num">1</div><h4>DUMMY TEXT OF THE PRINTING AND TYPESETTING</h4><p>Consectetur adipiscing elit. Pellentesque ut mollis lectus. Ut ultricies lacinia feugiat. Cras sed enim quis nunc condimentum ullamcorper. Aliquam eget lorem at purus porta volutpat in in enim. Fusce sollicitudin pulvinar rutrum. Etiam tempus porta mauris at fermentum.</p></div>
      <div class="step"><div class="step-num">2</div><h4>DUMMY TEXT OF THE PRINTING AND TYPESETTING</h4><p>Consectetur adipiscing elit. Pellentesque ut mollis lectus. Ut ultricies lacinia feugiat. Cras sed enim quis nunc condimentum ullamcorper. Aliquam eget lorem at purus porta volutpat in in enim.</p></div>
      <div class="step"><div class="step-num">3</div><h4>DUMMY TEXT OF THE PRINTING AND TYPESETTING</h4><p>Consectetur adipiscing elit. Pellentesque ut mollis lectus. Ut ultricies lacinia feugiat. Cras sed enim quis nunc condimentum ullamcorper. Aliquam eget lorem at purus porta volutpat in in enim.</p></div>
    </div>
  </section>

  <section class="team abs">
    <h2 class="section-title abs" style="top:30px">OUR TEAM</h2>
    <p class="team-sub abs" style="top:91px">Morbi leo risus, porta ac consectetur ac, vestibulum at eros.</p>

    <article class="card abs" style="left:112px;top:160px">
      <div class="photo" role="img" aria-label="Portrait of team member Orin Falke" style="background:linear-gradient(135deg,#3a3a3a,#4a4a4a 50%,#2a2a2a)"></div>
      <div class="badge"><svg width="14" height="14" viewBox="0 0 14 14"><path d="M2 3h10v6H7l-3 3V9H2z" fill="#fff"/></svg></div>
      <h3>ORIN FALKE</h3><div class="rule"></div>
      <p>Morbi leo risus, porta ac consectetur ac, vestibulum at eros. Lorem ipsum dolor sit amet, consectetur adipiscing elit.</p>
    </article>
    <article class="card featured abs" style="left:447px;top:160px">
      <div class="photo" role="img" aria-label="Portrait of team member Dario Wendt" style="background:linear-gradient(135deg,#3a3a3a,#555 50%,#333)"></div>
      <div class="badge"><svg width="14" height="14" viewBox="0 0 14 14"><path d="M2 3h10v6H7l-3 3V9H2z" fill="#fff"/></svg></div>
      <h3>DARIO WENDT</h3><div class="rule"></div>
      <p>Morbi leo risus, porta ac consectetur ac, vestibulum at eros. Lorem ipsum dolor sit amet, consectetur adipiscing elit.</p>
      <div class="socials"><i></i><i></i><i></i></div>
    </article>
    <article class="card abs" style="left:780px;top:160px">
      <div class="photo" role="img" aria-label="Portrait of team member Nadia Coyle" style="background:linear-gradient(135deg,#4a4a4a,#5a5a5a 50%,#3a3a3a)"></div>
      <div class="badge"><svg width="14" height="14" viewBox="0 0 14 14"><path d="M2 3h10v6H7l-3 3V9H2z" fill="#fff"/></svg></div>
      <h3>NADIA COYLE</h3><div class="rule"></div>
      <p>Morbi leo risus, porta ac consectetur ac, vestibulum at eros. Lorem ipsum dolor sit amet, consectetur adipiscing elit.</p>
    </article>

    <article class="card abs" style="left:112px;top:534px">
      <div class="photo" role="img" aria-label="Portrait of team member Orin Falke" style="background:linear-gradient(135deg,#6a6560,#4e4a46 50%,#3a3734)"></div>
      <div class="badge"><svg width="14" height="14" viewBox="0 0 14 14"><path d="M2 3h10v6H7l-3 3V9H2z" fill="#fff"/></svg></div>
      <h3>ORIN FALKE</h3><div class="rule"></div>
      <p>Morbi leo risus, porta ac consectetur ac, vestibulum at eros. Lorem ipsum dolor sit amet, consectetur adipiscing elit.</p>
    </article>
    <article class="card abs" style="left:447px;top:534px">
      <div class="photo" role="img" aria-label="Portrait of team member Mira Solvek" style="background:linear-gradient(135deg,#3f3f3f,#505050 50%,#2e2e2e)"></div>
      <div class="badge"><svg width="14" height="14" viewBox="0 0 14 14"><path d="M2 3h10v6H7l-3 3V9H2z" fill="#fff"/></svg></div>
      <h3>MIRA SOLVEK</h3><div class="rule"></div>
      <p>Morbi leo risus, porta ac consectetur ac, vestibulum at eros. Lorem ipsum dolor sit amet, consectetur adipiscing elit.</p>
    </article>
    <article class="card abs" style="left:780px;top:534px">
      <div class="photo" role="img" aria-label="Portrait of team member Hedda Brandt" style="background:linear-gradient(135deg,#4c4c4c,#6a655e 50%,#3c3c3c)"></div>
      <div class="badge"><svg width="14" height="14" viewBox="0 0 14 14"><path d="M2 3h10v6H7l-3 3V9H2z" fill="#fff"/></svg></div>
      <h3>HEDDA BRANDT</h3><div class="rule"></div>
      <p>Morbi leo risus, porta ac consectetur ac, vestibulum at eros. Lorem ipsum dolor sit amet, consectetur adipiscing elit.</p>
    </article>
  </section>

  <section class="banner abs" role="img" aria-label="Blue-tinted photo of a team reviewing charts at a table">
    <h2 class="abs" style="top:150px">VARNOTH SIGNAL<br>RELIES ON STATE OF THE ART ANALYTICS</h2>
    <div class="btn btn-outline abs">BUY NOW</div>
  </section>

  <section class="analytics-head abs">
    <h2 class="abs" style="top:30px">ANALYTICS</h2>
    <p class="abs" style="top:80px">simply dummy text of the printing and typesetting</p>
  </section>
  <div class="laptop abs" role="img" aria-label="Hands typing on a laptop showing analytics charts"></div>
  <p class="analytics-copy abs">It is a long established fact that a reader will be distracted by the readable content of a page when looking at its layout. The point of using Lorem Ipsum is that it has a more-or-less normal distribution of letters, as opposed to using 'Content here, content here', making it look like readable English.</p>
  <div class="stat-row abs">
    <div class="stat active"><small>SIMPLY DUMMY TEXT</small><strong>ANALYTICS</strong></div>
    <div class="stat"><small>SIMPLY DUMMY TEXT</small><strong>ANALYTICS</strong></div>
    <div class="stat"><small>SIMPLY DUMMY TEXT</small><strong>ANALYTICS</strong></div>
  </div>

  <footer class="footer abs">
    <div class="foot-col abs" style="left:110px;top:56px">
      <div>Copyright 2017-18 <span class="brand">Varnoth Signal</span></div>
      <div>Designed and developed in-house</div>
      <div class="foot-social"><i></i><i></i><i></i><i></i></div>
    </div>
    <div class="foot-col abs" style="left:445px;top:56px">
      <h4>Our location</h4>
      <div>Varnoth Signal LLC 0000 Alder Row,<br>Suite 112 Fenmore, IL 00000</div>
      <div style="margin-top:6px">Phone : +00 1 55501234</div>
      <div>Email : info@varnothsignal.example</div>
    </div>
    <div class="foot-col abs" style="left:780px;top:56px">
      <h4>Keep in touch</h4>
      <div style="width:320px">Lorem ipsum dolor sit amet, consectetur adi sollicitud ante tellus ornare mi, et mollis</div>
      <div class="subscribe">Your email<svg width="10" height="10" viewBox="0 0 10 10"><path d="M1 5h7M5 2l3 3-3 3" fill="none" stroke="#aaa" stroke-width="1.3"/></svg></div>
    </div>
    <div class="bottom-bar abs">
      <svg class="abs" style="left:590px;top:16px" width="20" height="14" viewBox="0 0 20 14"><path d="M4 10l6-6 6 6" fill="none" stroke="#fff" stroke-width="2.5"/></svg>
    </div>
  </footer>

</div>
</body>
</html>
```